Redesign This Psychology Website

We would like a slight redesign of this successful psychology (relationship counselling) website:

www.TheKelvaleClinic.com.au

We are updating the website, and we'd like a slight refresh of the design and style.

Please keep to very similar colours, and use the same logo. We're looking for around 10 page templates, however the main one is the home page.

Keep in mind, this website already converts quite well, so we want a new, fresh design in keeping with this one. Please don't bother designing something too extremely different.

thanks :)

Target Market(s)

couples who are looking for relationship counselling. Men and women, 25 - 70, across Australia

Industry/Entity Type

Psychology

Number of Pages Required

5+ page

Font styles to use
Sans Serif

Colors
87cfc6
b7a5cd
ec1f27
ffffff
cee9f5

Requirements
Must have
• a similar look to the current design, just looking for a slight refresh.
• Search bar
• Areas for lots of photos
• same logo
• lots of content areas
Nice to have
• great content areas, where we can display a lot of content and our areas.
Should not have
• no colors like orange, etc.
• should not have a totally different feel.

```html
<!DOCTYPE html>
<html lang="en">
<head>
<meta charset="utf-8">
<title>The Kelvale Clinic – Relationship Counselling</title>
<link href="https://fonts.googleapis.com/css2?family=Open+Sans:wght@400;600;700&family=Roboto+Condensed:wght@400;700&display=swap" rel="stylesheet">
<style>
:root{
  --teal:#1a8fa0;
  --teal-dark:#157a89;
  --teal-light:#87cfc6;
  --red:#ec1f27;
  --ink:#222;
  --grey:#666;
  --line:#e2e2e2;
  --footer:#f3f3f3;
  --nav-active:#2f3b40;
  --white:#fff;
}
*{box-sizing:border-box;margin:0;padding:0}
html,body{width:1200px;height:3209px;overflow:hidden;background:var(--white)}
body{font-family:"Open Sans",Arial,sans-serif;color:var(--ink)}
.page{position:relative;width:1200px;height:3209px;overflow:hidden}
.abs{position:absolute}

/* header */
.brand{left:96px;top:30px;display:flex;align-items:center;gap:14px}
.brand-dot{width:60px;height:60px;border-radius:50%;background:var(--teal)}
.brand-name{font-family:"Roboto Condensed",sans-serif;font-size:36px;color:var(--teal);line-height:1}
.brand-tag{font-size:14px;color:var(--teal);margin-top:6px}
.phone{left:631px;top:66px;font-family:"Roboto Condensed",sans-serif;font-size:17px;color:var(--red);display:flex;align-items:center;gap:8px;white-space:nowrap}
.search{left:866px;top:62px;width:234px;height:36px;border:1px solid #ccc;border-radius:3px;font-size:13px;color:#555;padding:8px 12px;display:flex;justify-content:space-between;align-items:center}

/* nav */
.nav{left:0;top:157px;width:1200px;height:53px;background:linear-gradient(var(--teal),var(--teal-dark))}
.nav ul{list-style:none;display:flex;margin-left:100px;height:53px}
.nav li{font-family:"Roboto Condensed",sans-serif;font-size:14px;color:var(--white);padding:0 17px;line-height:53px;text-transform:uppercase}
.nav li.active{background:var(--nav-active);padding:0 22px}

/* hero */
.hero{left:0;top:210px;width:1200px;height:545px;background:linear-gradient(160deg,#7fae52 0%,#a7c86a 35%,#e6dcc0 60%,#4f7a3a 100%)}
.hero-arrow{width:34px;height:34px;border-radius:50%;background:rgba(0,0,0,.55);display:flex;align-items:center;justify-content:center}
.finder{left:802px;top:325px;width:298px;height:300px;background:rgba(233,70,70,.85);padding:22px 22px}
.finder h2{font-family:"Roboto Condensed",sans-serif;font-size:23px;color:var(--white);line-height:1.15;margin-bottom:14px}
.field{height:38px;background:var(--white);border-radius:2px;font-size:12px;color:#777;padding:10px 10px;margin-bottom:12px;display:flex;justify-content:space-between}
.btn-dark{display:inline-block;background:#2b2b2b;color:var(--white);font-family:"Roboto Condensed",sans-serif;font-size:14px;padding:8px 16px}

/* welcome */
.video{left:124px;top:785px;width:447px;height:338px;background:linear-gradient(90deg,#3d6fa3 0%,#5b87b5 45%,#8a7a66 60%,#6b5a48 100%)}
.play{left:308px;top:946px;width:52px;height:52px;border-radius:50%;background:rgba(0,0,0,.45);display:flex;align-items:center;justify-content:center}
.welcome{left:601px;top:848px;width:500px}
.welcome h1{font-family:"Roboto Condensed",sans-serif;font-weight:400;font-size:34px;color:#333;margin-bottom:14px}
.welcome .lead{font-size:14.5px;line-height:1.5;color:#333;margin-bottom:14px}
.welcome p{font-size:11.5px;line-height:1.65;color:var(--grey);margin-bottom:12px}
.btn-teal{display:inline-block;background:var(--teal);color:var(--white);font-family:"Roboto Condensed",sans-serif;font-size:13px;padding:9px 16px;border-radius:2px;margin-top:8px}

/* services */
.services-title{left:0;top:1216px;width:1200px;text-align:center;font-family:"Roboto Condensed",sans-serif;font-size:36px;color:#222}
.services-sub{left:270px;top:1274px;width:660px;text-align:center;font-size:11.5px;line-height:1.6;color:#555}
.service{top:1365px;width:260px;text-align:center}
.service-photo{width:197px;height:197px;border-radius:50%;margin:0 auto;position:relative}
.heart-badge{position:absolute;left:80px;bottom:-18px;width:38px;height:38px;border-radius:50%;background:var(--red);border:3px solid var(--white);display:flex;align-items:center;justify-content:center}
.service h3{font-family:"Roboto Condensed",sans-serif;font-weight:400;font-size:15px;color:#222;margin-top:40px;text-transform:uppercase}
.service p{font-size:11.5px;line-height:1.55;color:#555;margin:10px auto 0;width:200px}
.chev{margin-top:10px}

/* specialise */
.special-band{left:0;top:1780px;width:1200px;height:494px;background:linear-gradient(180deg,#1e8fa0,#18778a)}
.special-title{left:98px;top:1890px;width:520px;font-family:"Roboto Condensed",sans-serif;font-weight:700;font-size:31px;line-height:1.25;color:var(--white);text-transform:uppercase}
.special-text{left:98px;top:1985px;width:520px;font-size:11.5px;line-height:1.75;color:#e6f4f6}
.special-text p{margin-bottom:14px}
.btn-outline{left:98px;top:2156px;border:1px solid rgba(255,255,255,.8);color:var(--white);font-family:"Roboto Condensed",sans-serif;font-size:13px;padding:8px 16px}
.special-photo{left:644px;top:1887px;width:456px;height:310px;border:5px solid var(--white);background:linear-gradient(120deg,#d9d3cc,#c9a58e 45%,#f2eae6)}

/* news */
.news-title{left:98px;top:2352px;font-family:"Roboto Condensed",sans-serif;font-size:30px;color:#222}
.news-ctrl{top:2360px;width:22px;height:22px;border:1px solid #ccc;display:flex;align-items:center;justify-content:center}
.news-item{left:100px;width:680px;display:flex;gap:22px}
.news-thumb{width:215px;height:140px;flex:none}
.news-body h3{font-family:"Roboto Condensed",sans-serif;font-weight:400;font-size:19px;color:#222;margin-top:4px}
.news-date{font-family:"Roboto Condensed",sans-serif;font-size:13px;color:var(--red);margin:10px 0 8px}
.news-body p{font-size:11.5px;line-height:1.7;color:#555;padding-bottom:14px;border-bottom:1px solid var(--line)}
.ad{left:856px;width:246px;height:192px;position:absolute}
.ad-head{position:absolute;font-family:"Roboto Condensed",sans-serif;font-weight:700;font-style:italic;font-size:21px;line-height:1.1}
.ad-bar{position:absolute;left:0;bottom:0;width:100%;color:var(--white);font-size:12px;line-height:1.3;padding:4px 6px}

/* footer */
.footer{left:0;top:2841px;width:1200px;height:308px;background:var(--footer);border-top:1px solid #ddd}
.foot-brand{left:100px;top:2935px;display:flex;align-items:center;gap:10px}
.foot-brand .brand-dot{width:40px;height:40px}
.foot-brand .brand-name{font-size:24px}
.socials{left:146px;top:2998px;display:flex;gap:5px}
.socials span{width:20px;height:20px;border-radius:50%;border:1px solid #999}
.foot-h{font-family:"Roboto Condensed",sans-serif;font-size:17px;color:#222;text-transform:uppercase}
.quick{left:327px;top:2898px}
.quick ul{list-style:none;margin-top:22px}
.quick li{font-size:11px;color:#444;line-height:22px;display:flex;align-items:center;gap:8px}
.quick li::before{content:"";width:8px;height:8px;border-radius:50%;border:2px solid var(--teal)}
.newsletter{left:537px;top:2898px;width:292px}
.newsletter p{font-size:11px;line-height:1.6;color:#555;margin:20px 0 14px}
.input{height:38px;background:var(--white);border:1px solid #ddd;font-size:11px;color:#555;padding:11px 12px;margin-bottom:10px}
.sub-row{display:flex}
.sub-row .input{flex:1;margin:0}
.subscribe{background:var(--red);color:var(--white);font-family:"Roboto Condensed",sans-serif;font-size:13px;padding:11px 12px;height:38px}
.contact{left:898px;top:2898px;width:250px}
.contact .addr{font-size:12px;line-height:1.6;color:#444;margin:24px 0 12px}
.contact .row{display:flex;align-items:center;gap:12px;font-size:12px;color:#444;margin-bottom:12px}
.bottom{left:0;top:3149px;width:1200px;height:60px;background:var(--white);border-top:1px solid #ddd;text-align:center;font-size:11px;color:#444;line-height:60px}
</style>
</head>
<body>
<div class="page">

  <!-- header -->
  <div class="abs brand">
    <span class="brand-dot"></span>
    <div>
      <div class="brand-name">The Kelvale Clinic</div>
      <div class="brand-tag">helping you create loving relationships</div>
    </div>
  </div>
  <div class="abs phone">
    <svg width="16" height="16" viewBox="0 0 24 24"><path fill="#ec1f27" d="M6.6 10.8a15.1 15.1 0 0 0 6.6 6.6l2.2-2.2c.3-.3.7-.4 1-.2 1.1.4 2.3.6 3.6.6.6 0 1 .4 1 1V20c0 .6-.4 1-1 1A17 17 0 0 1 3 4c0-.6.4-1 1-1h3.5c.6 0 1 .4 1 1 0 1.3.2 2.5.6 3.6.1.3 0 .7-.2 1z"/></svg>
    CALL US ON 1300 555 014
  </div>
  <div class="abs search">search
    <svg width="12" height="12" viewBox="0 0 24 24"><circle cx="10" cy="10" r="6.5" fill="none" stroke="#333" stroke-width="3"/><path d="M15 15l6 6" stroke="#333" stroke-width="3"/></svg>
  </div>

  <nav class="abs nav">
    <ul>
      <li class="active">Home</li><li>About</li><li>Counselling Types</li><li>Sex Therapy Locations</li><li>Quizzes</li><li>F.A.Q.'s</li><li>Resources</li><li>Blog</li><li>Shop</li><li>Contact</li>
    </ul>
  </nav>

  <!-- hero -->
  <div class="abs hero" role="img" aria-label="Happy couple laughing together outdoors among green trees"></div>
  <svg class="abs" style="left:0;top:660px" width="1200" height="100" viewBox="0 0 1200 100" preserveAspectRatio="none">
    <path d="M0 65 C250 20 500 30 750 55 S1050 40 1200 20 V100 H0Z" fill="#1a8fa0"/>
    <path d="M0 80 C250 35 500 45 750 68 S1050 55 1200 40 V100 H0Z" fill="#87cfc6"/>
    <path d="M0 92 C250 50 500 60 750 80 S1050 70 1200 58 V100 H0Z" fill="#fff"/>
  </svg>
  <div class="abs hero-arrow" style="left:37px;top:454px"><svg width="12" height="12" viewBox="0 0 12 12"><path d="M8 1L3 6l5 5" stroke="#fff" stroke-width="2" fill="none"/></svg></div>
  <div class="abs hero-arrow" style="left:1139px;top:454px"><svg width="12" height="12" viewBox="0 0 12 12"><path d="M4 1l5 5-5 5" stroke="#fff" stroke-width="2" fill="none"/></svg></div>
  <div class="abs finder">
    <h2>FIND OUR PSYCHOLOGIST<br>NEAR YOU</h2>
    <div class="field">Type of Counselling <span>&#8597;</span></div>
    <div class="field">Location</div>
    <div class="field">Postcode</div>
    <span class="btn-dark">SEARCH</span>
  </div>

  <!-- welcome -->
  <div class="abs video" role="img" aria-label="Video still of a counsellor speaking to camera"></div>
  <div class="abs play"><svg width="18" height="18" viewBox="0 0 18 18"><path d="M5 3l10 6-10 6z" fill="#fff"/></svg></div>
  <div class="abs welcome">
    <h1>WELCOME TO THE KELVALE CLINIC</h1>
    <p class="lead">The Kelvale Clinic is a company passionate about creating healthy loving relationships, of all kinds.</p>
    <p>Our mission is to be the most highly regarded relationship help service in Australia, by delivering a comprehensive range of the highest quality relationship and marriage counselling and advice, and books and products to educate and enhance client's relationships.</p>
    <p>To have every client who comes through our doors leave feeling listened to, understood, and educated on how to build a better relationship with their partner</p>
    <span class="btn-teal">READ MORE</span>
  </div>

  <!-- services -->
  <div class="abs services-title">Our Services</div>
  <div class="abs services-sub">Sed ut perspiciatis unde omnis iste natus error sit voluptatem accusantium doloremque laudantium, totam rem aperiam, eaque ipsa quae ab illo inventore veritatis et quasi architecto beatae vitae dicta sunt explicabo.</div>

  <div class="abs service" style="left:69px">
    <div class="service-photo" role="img" aria-label="Couple in a counselling session" style="background:linear-gradient(135deg,#c9b8a8,#8c6f5c)">
      <span class="heart-badge"><svg width="16" height="14" viewBox="0 0 16 14"><path d="M8 14L1.5 7.5A4 4 0 0 1 8 2.5a4 4 0 0 1 6.5 5z" fill="#fff"/></svg></span>
    </div>
    <h3>Relationship Counselling</h3>
    <p>Communication, Recovering from an affair, Loss of intimacy &amp; love, Power battles, Feeling like friends</p>
    <svg class="chev" width="12" height="12" viewBox="0 0 12 12"><path d="M2 2l4 4 4-4M2 6l4 4 4-4" stroke="#333" stroke-width="1.5" fill="none"/></svg>
  </div>
  <div class="abs service" style="left:328px">
    <div class="service-photo" role="img" aria-label="Couple holding red heart balloons" style="background:linear-gradient(135deg,#e8d9cf,#d43a3a)">
      <span class="heart-badge"><svg width="16" height="14" viewBox="0 0 16 14"><path d="M8 14L1.5 7.5A4 4 0 0 1 8 2.5a4 4 0 0 1 6.5 5z" fill="#fff"/></svg></span>
    </div>
    <h3>Sex Therapy Counselling</h3>
    <p>Sex and lovemaking can be the most delicious or dissatisfying part of your life and your relationship.</p>
    <svg class="chev" width="12" height="12" viewBox="0 0 12 12"><path d="M2 2l4 4 4-4M2 6l4 4 4-4" stroke="#333" stroke-width="1.5" fill="none"/></svg>
  </div>
  <div class="abs service" style="left:599px">
    <div class="service-photo" role="img" aria-label="Frustrated man in an office" style="background:linear-gradient(135deg,#4a6fa6,#9aa6b5)">
      <span class="heart-badge"><svg width="16" height="14" viewBox="0 0 16 14"><path d="M8 14L1.5 7.5A4 4 0 0 1 8 2.5a4 4 0 0 1 6.5 5z" fill="#fff"/></svg></span>
    </div>
    <h3>Anger Management</h3>
    <p>Communication, Recovering from an affair, Loss of intimacy &amp; love, Power battles, Feeling like friends</p>
    <svg class="chev" width="12" height="12" viewBox="0 0 12 12"><path d="M2 2l4 4 4-4M2 6l4 4 4-4" stroke="#333" stroke-width="1.5" fill="none"/></svg>
  </div>
  <div class="abs service" style="left:869px">
    <div class="service-photo" role="img" aria-label="Man with multiple reflected expressions" style="background:linear-gradient(135deg,#b79a88,#5a4a42)">
      <span class="heart-badge"><svg width="16" height="14" viewBox="0 0 16 14"><path d="M8 14L1.5 7.5A4 4 0 0 1 8 2.5a4 4 0 0 1 6.5 5z" fill="#fff"/></svg></span>
    </div>
    <h3>Narcissism Counselling</h3>
    <p>Communication, Recovering from an affair, Loss of intimacy &amp; love, Power battles, Feeling like friends</p>
    <svg class="chev" width="12" height="12" viewBox="0 0 12 12"><path d="M2 2l4 4 4-4M2 6l4 4 4-4" stroke="#333" stroke-width="1.5" fill="none"/></svg>
  </div>

  <!-- specialise -->
  <div class="abs special-band" role="img" aria-label="Soft teal-tinted outdoor background"></div>
  <svg class="abs" style="left:0;top:1770px" width="1200" height="60" viewBox="0 0 1200 60" preserveAspectRatio="none">
    <path d="M0 0 H1200 V30 C950 5 700 0 450 25 S150 35 0 20Z" fill="#fff"/>
    <path d="M0 20 C150 35 300 40 450 25 S950 5 1200 30" stroke="#8cc63f" stroke-width="3" fill="none"/>
  </svg>
  <h2 class="abs special-title">We specialise in relationship<br>&amp; marriage counselling</h2>
  <div class="abs special-text">
    <p>At the Kelvale Clinic, we are a group of PSYCHOLOGISTS, Australia wide who are passionate about relationships and helping you with yours. Our vision is to provide the most highly regarded and comprehensive marriage counselling and relationship counselling, and sex therapy in Australia, at reasonable and affordable rates.</p>
    <p>When we are experiencing relationship and marriage problems, there can be a lot of pain and confusion, and it can often be difficult to cope with the other areas of our lives when we are struggling with problems with our partner.</p>
  </div>
  <span class="abs btn-outline">READ MORE</span>
  <div class="abs special-photo" role="img" aria-label="Young couple smiling during a session with a counsellor"></div>
  <svg class="abs" style="left:1030px;top:2140px" width="65" height="52" viewBox="0 0 65 52"><path d="M65 0V52H0Z" fill="#1a8fa0"/></svg>

  <!-- news -->
  <div class="abs news-title">LATEST NEWS</div>
  <div class="abs news-ctrl" style="left:738px"><svg width="8" height="8" viewBox="0 0 8 8"><path d="M5 1L2 4l3 3" stroke="#333" stroke-width="1.5" fill="none"/></svg></div>
  <div class="abs news-ctrl" style="left:764px"><svg width="8" height="8" viewBox="0 0 8 8"><path d="M3 1l3 3-3 3" stroke="#333" stroke-width="1.5" fill="none"/></svg></div>

  <div class="abs news-item" style="top:2422px">
    <div class="news-thumb" role="img" aria-label="Woman looking away from her partner" style="background:linear-gradient(120deg,#7a6a60,#d8c8bc)"></div>
    <div class="news-body">
      <h3>Why am I with a Narcissist?</h3>
      <div class="news-date">FEBRUARY 24, 2017</div>
      <p>You may be wondering why anyone would be masochistic enough to ever get themselves into a relationship with someone who has so many characteristics of a narcissist and who leaves you feeling so dreadful?</p>
    </div>
  </div>
  <div class="abs news-item" style="top:2603px">
    <div class="news-thumb" role="img" aria-label="Upset woman on a sofa beside her partner" style="background:linear-gradient(120deg,#a86a55,#e3d5cc)"></div>
    <div class="news-body">
      <h3>How Do I Know If I'm With a Narcissist?</h3>
      <div class="news-date">FEBRUARY 24, 2017</div>
      <p>An integral part of a healthy relationship is a sense of equality and consideration and empathy for each other. In fact no relationship can feel rewarding and supportive if either partner is mostly self-absorbed.</p>
    </div>
  </div>

  <div class="ad" style="top:2362px;background:linear-gradient(90deg,#f3ece6,#e2cfc4)">
    <div class="ad-head" style="left:8px;top:10px;color:#d42a2a">Is Anxiety,<br>Depression<br>or Stress<br>bothering<br>YOU?</div>
    <div class="ad-bar" style="background:#d42a2a">Click here for help from Kelvale Anxiety &amp; Depression Psychologists</div>
  </div>
  <div class="ad" style="top:2560px;background:linear-gradient(90deg,#d7e6ee,#f1f5f7)">
    <div class="ad-head" style="right:8px;top:70px;color:#1d3f5e;text-align:right">Information<br>for referring<br>GPs &amp; health<br>professionals</div>
    <div class="ad-bar" style="background:#1a8fa0">Click here for more details.</div>
  </div>

  <!-- footer -->
  <footer class="abs footer"></footer>
  <div class="abs foot-brand"><span class="brand-dot"></span><span class="brand-name">The Kelvale Clinic</span></div>
  <div class="abs socials"><span></span><span></span><span></span><span></span><span></span></div>

  <div class="abs quick">
    <div class="foot-h">Quick Links</div>
    <ul>
      <li>Home</li><li>Counselling Types</li><li>Relationship Counselling</li><li>Sex Therapy Locations</li><li>Quizzes</li><li>F.A.Q.'s</li><li>Contact</li>
    </ul>
  </div>
  <div class="abs newsletter">
    <div class="foot-h">Sign up for Newsletter</div>
    <p>Sed ut perspiciatis unde omnis iste natus error sit voluptatem accusantium doloremque</p>
    <div class="input">Enter Name</div>
    <div class="sub-row"><div class="input">Enter Email</div><div class="subscribe">SUBSCRIBE</div></div>
  </div>
  <div class="abs contact">
    <div class="foot-h">Contact Us</div>
    <div class="addr">The Kelvale Clinic 2017<br>12 Harbour Lane Kelvale<br>VIC 3081</div>
    <div class="row"><svg width="16" height="16" viewBox="0 0 24 24"><path fill="#1a8fa0" d="M6.6 10.8a15.1 15.1 0 0 0 6.6 6.6l2.2-2.2c.3-.3.7-.4 1-.2 1.1.4 2.3.6 3.6.6.6 0 1 .4 1 1V20c0 .6-.4 1-1 1A17 17 0 0 1 3 4c0-.6.4-1 1-1h3.5c.6 0 1 .4 1 1 0 1.3.2 2.5.6 3.6.1.3 0 .7-.2 1z"/></svg>Phone : 1300 555 014</div>
    <div class="row"><svg width="16" height="12" viewBox="0 0 16 12"><rect x="1" y="1" width="14" height="10" fill="none" stroke="#1a8fa0" stroke-width="1.5"/><path d="M1 1l7 6 7-6" fill="none" stroke="#1a8fa0" stroke-width="1.5"/></svg>info@thekelvaleclinic.com.au</div>
  </div>

  <div class="abs bottom">©2017 The Kelvale Clinic., All Rights Reserved.</div>
</div>
</body>
</html>
```